Nanny Share Ecommerce Website for Finding Childcare and Parents who need Childcare BrightPramHub.net

Our company needs an ecommerce website (BrightPramHub.net) for a US subscription based service strictly for nanny sharing that connects families and caregivers. The website would allow families to connect with one another as well as to search for nannies. The service would be searchable for other families by location (by radius or zip code), children demographic (age range/gender/special needs), days of week or times, after school care, school closure days (holidays), etc. The service would also be searchable for nannies based on gender, provider age range, years experience, language, hourly rate, transportation available, certification (CPR first aid), education etc. The search fields would be searchable and sortable and allow to connect with the provider (after paying subscription fee). The service would be similar to tendlyfolk.net in that it would allow for families and caregivers to post photos as well as a short bio of the themselves. There would also be a feedback/star rating mechanism to rate caregivers who have performed work for families (viewable to public). The service would be free for nannies to post their bios and only a subscription based service for families to connect with other families or with caregivers (able to view bio but need service to connect). There will be a short bio on the benefits of nanny sharing (reduced cost, increased flexibility for parents, reduced illness, increased socialization with other children vs. sole nanny), as well as Q&A section with best practices.

Target Market(s)

Families, Nannies

Industry/Entity Type

Childcare

Logo Text

Bright Pram Hub

Coding

Coded - Design and coding required

Number of Pages Required

5+ page

Requirements
Must have
• Searchable (need to be able to search for families as well as nannies), responsive, functional, easy to use, add value to families and nannies. Needs to be able to collect payment for subscription.
Nice to have
• Optimized for mobile, SEO optimized

```html
<!DOCTYPE html>
<html lang="en">
<head>
<meta charset="utf-8">
<title>Bright Pram Hub — Connects Families to Share Caregivers</title>
<link href="https://fonts.googleapis.com/css2?family=Raleway:wght@300;400;600&family=Lato:wght@400;700&display=swap" rel="stylesheet">
<style>
:root{
  --pink:#e8329a;
  --pink-deep:#d81b7f;
  --orange:#f4511e;
  --orange-soft:#ff6a3d;
  --purple:#8c3a9e;
  --ink:#222;
  --black:#111;
  --grey:#777;
  --line:#ddd;
  --white:#fff;
}
*{box-sizing:border-box;margin:0;padding:0}
html,body{width:1200px;height:3846px;overflow:hidden}
body{position:relative;font-family:'Lato',sans-serif;color:var(--ink);background:var(--white)}
.abs{position:absolute}
.heading{font-family:'Raleway',sans-serif;font-weight:300;text-align:center}

/* top bar */
.topbar{left:0;top:0;width:1200px;height:20px;background:linear-gradient(90deg,var(--pink),var(--orange-soft));display:flex;justify-content:flex-end;align-items:center;padding-right:85px;gap:18px;font-size:11px;color:var(--white)}
.topbar span.sep{opacity:.7}

/* hero */
.hero{left:0;top:20px;width:1200px;height:544px;background:#f5f1ee;overflow:hidden}
.hero-photo{position:absolute;left:380px;top:0;width:820px;height:544px;background:radial-gradient(ellipse at 45% 40%,#e9c3a8 0%,#d8b49a 30%,#efe8e2 70%,#f7f4f1 100%)}
.brand{display:flex;align-items:center;gap:10px;font-family:'Lato',sans-serif;font-weight:700;color:var(--pink)}
.brand .dot{border-radius:50%;background:var(--pink)}
.hero .brand{position:absolute;left:90px;top:90px;font-size:24px}
.hero .brand .dot{width:44px;height:44px}
.tagline{position:absolute;left:87px;top:212px;font-family:'Raleway',sans-serif;font-weight:400;font-size:26px;line-height:35px;color:var(--ink)}
.choice{position:absolute;left:290px;top:313px;width:620px;height:187px;border:2px solid #f0a6cf;background:rgba(255,255,255,.82);text-align:center}
.choice p{font-family:'Raleway',sans-serif;font-size:28px;color:#444;margin-top:42px}
.choice .btns{display:flex;justify-content:center;gap:25px;margin-top:22px}
.btn{display:inline-block;width:162px;height:46px;line-height:46px;color:var(--white);font-size:17px;text-align:center}
.btn-care{background:var(--pink)}
.btn-nanny{background:#333}

/* nav */
.nav{left:0;top:564px;width:1200px;height:64px;background:var(--black);display:flex;justify-content:center;align-items:center;gap:42px;color:var(--white);font-size:13px}

/* offer */
.offer-title{left:0;top:700px;width:1200px;font-size:40px;color:#333}
.offer-card{top:774px;width:433px;height:244px;overflow:hidden}
.offer-card .ph{width:100%;height:100%}
.offer-card h3{position:absolute;left:38px;bottom:38px;font-size:17px;color:var(--white);font-weight:700}
.offer-card small{position:absolute;left:38px;bottom:18px;font-size:11px;color:var(--white)}

/* benefits */
.benefits{left:0;top:1097px;width:1200px;height:582px;background:linear-gradient(100deg,#9a3fa6 0%,#b3479a 45%,#d9583f 100%);overflow:hidden}
.benefits-title{left:0;top:75px;width:1200px;font-size:38px;color:var(--white)}
.benefit{width:235px;color:var(--white)}
.benefit h4{font-size:17px;font-weight:700;line-height:21px;text-transform:uppercase}
.benefit p{font-size:11px;line-height:16px;margin-top:8px;opacity:.9}
.benefit.left{text-align:right}
.icon-dot{width:76px;height:76px;border-radius:50%;background:var(--orange);display:flex;align-items:center;justify-content:center}
.hub{left:467px;top:208px;width:266px;height:266px;border-radius:50%;background:var(--white);display:flex;align-items:center;justify-content:center}
.hub .brand{font-size:19px}
.hub .brand .dot{width:36px;height:36px}

/* blog */
.blog-title{left:0;top:1760px;width:1200px;font-size:40px;color:#333}
.blog-card{top:1838px;width:326px;height:331px;overflow:hidden}
.blog-card .ph{width:100%;height:100%}
.blog-card h3{position:absolute;left:18px;top:218px;width:250px;font-size:18px;line-height:25px;color:var(--white);font-weight:700}
.blog-card small{position:absolute;left:18px;top:287px;font-size:12px;color:var(--white);font-weight:700}

/* testimonial */
.testimonial{left:0;top:2256px;width:1200px;height:282px;background:linear-gradient(90deg,#f14fb4 0%,#e94aa6 45%,#f9735a 100%)}
.avatar{left:90px;top:47px;width:138px;height:138px;border-radius:50%;border:4px solid var(--white);background:radial-gradient(circle at 50% 40%,#c9a28a,#8d6a58)}
.stars{left:113px;top:196px}
.divider{left:256px;top:40px;width:2px;height:175px;background:rgba(255,255,255,.7)}
.quote{left:300px;top:56px;width:800px;font-size:14px;line-height:23px;color:var(--white)}
.author{left:300px;top:145px;font-family:'Raleway',sans-serif;font-size:24px;color:var(--white)}
.pager{left:316px;top:210px;display:flex;gap:10px}
.pager span{width:26px;height:26px;display:flex;align-items:center;justify-content:center}
.pager .prev{background:var(--white)}
.pager .next{background:#222}

/* faq */
.faq-title{left:0;top:2600px;width:1200px;font-size:40px;color:#333}
.faq{left:179px;width:842px}
.faq .q{display:flex;justify-content:space-between;align-items:center;padding:0 22px;color:var(--white);font-size:14px;font-weight:700;height:51px;background:var(--black);border-radius:3px}
.faq.open{background:var(--orange);border-radius:3px;height:138px}
.faq.open .q{background:transparent}
.faq.open .a{padding:0 22px 22px;color:var(--white);font-size:11.5px;line-height:18px}

/* newsletter */
.newsletter{left:0;top:3166px;width:1200px;height:326px;background:linear-gradient(180deg,#1d2330 0%,#2b3342 55%,#1a1f29 100%)}
.nl-title{left:0;top:66px;width:1200px;font-size:35px;letter-spacing:6px;color:var(--white);font-weight:400}
.nl-sub{left:0;top:115px;width:1200px;text-align:center;font-size:13px;line-height:19px;color:#e6e6e6}
.nl-input{left:305px;top:172px;width:413px;height:48px;background:var(--white);font-size:12px;color:#999;padding:16px 18px}
.nl-btn{left:738px;top:172px;width:162px;height:48px;background:var(--pink);color:var(--white);font-size:14px;font-weight:700;letter-spacing:2px;display:flex;align-items:center;justify-content:center}
.social{left:491px;top:247px;display:flex;gap:12px}
.social span{width:36px;height:36px;border-radius:50%}

/* footer */
.footer{left:0;top:3492px;width:1200px;height:354px;background:var(--white)}
.footer .brand{position:absolute;left:90px;top:100px;font-size:27px}
.footer .brand .dot{width:56px;height:56px}
.vline{top:65px;width:1px;height:200px;background:var(--line)}
.foot-h{font-size:17px;color:#555;font-weight:400}
.contact{left:531px;top:70px}
.contact ul{list-style:none;margin-top:22px;font-size:13px;color:#666;line-height:20px}
.contact li{display:flex;gap:18px;margin-bottom:16px}
.links{left:1005px;top:70px}
.links ul{list-style:none;margin-top:22px;font-size:11px;color:#666;line-height:17px}
.footline{left:87px;top:290px;width:1026px;height:1px;background:var(--line)}
.copy{left:0;top:311px;width:1200px;text-align:center;font-size:12px;color:#888}
</style>
</head>
<body>

<div class="abs topbar"><span>Log In</span><span class="sep">|</span><span>Join Now</span><span class="sep">|</span><span>For Businesses</span></div>

<section class="abs hero">
  <div class="hero-photo" role="img" aria-label="Photo of a mother and daughter drawing together at a table"></div>
  <div class="brand"><span class="dot"></span>Bright Pram Hub</div>
  <h1 class="tagline">Connects Families<br>to Share Caregivers</h1>
  <div class="choice">
    <p>Let's get started. Choose an option.</p>
    <div class="btns"><span class="btn btn-care">Find Care</span><span class="btn btn-nanny">Find Nanny</span></div>
  </div>
</section>

<nav class="abs nav"><span>What We Offer</span><span>Child Care</span><span>Senior Care</span><span>Pet Care</span><span>Housekeeping</span><span>How It Works</span><span>Contact US</span></nav>

<h2 class="abs heading offer-title">What we offer</h2>
<div class="abs offer-card" style="left:154px">
  <div class="ph" role="img" aria-label="Photo of a smiling woman and girl outdoors" style="background:linear-gradient(120deg,#6f8a5a,#c9b08d 55%,#e7d6c3)"></div>
  <h3>Matching Families</h3>
</div>
<div class="abs offer-card" style="left:613px">
  <div class="ph" role="img" aria-label="Photo of a nanny playing with a child" style="background:linear-gradient(120deg,#8d3c9f,#c05a9a 55%,#e592b8)"></div>
  <h3>Helping Connect Families to Nannies</h3>
  <small>&#9654; Get started</small>
</div>

<section class="abs benefits" role="img" aria-label="Background photo of a parent and child laughing, tinted purple to orange">
  <h2 class="abs heading benefits-title">Our Benefits</h2>
  <svg class="abs" style="left:0;top:0" width="1200" height="582" viewBox="0 0 1200 582">
    <circle cx="600" cy="341" r="150" fill="none" stroke="#fff" stroke-width="2" stroke-dasharray="6 6"/>
    <g stroke="#fff" stroke-width="4" fill="none" stroke-linecap="round">
      <path d="M490 240 L455 208 M455 208 l18 0 M455 208 l0 18"/>
      <path d="M710 240 L745 208 M745 208 l-18 0 M745 208 l0 18"/>
      <path d="M490 442 L455 474 M455 474 l18 0 M455 474 l0 -18"/>
      <path d="M710 442 L745 474 M745 474 l-18 0 M745 474 l0 -18"/>
    </g>
  </svg>
  <div class="abs hub"><div class="brand"><span class="dot"></span>Bright Pram Hub</div></div>

  <div class="abs benefit left" style="left:80px;top:164px"><h4>Reduced Cost</h4><p>Sed ut perspiciatis unde omnis iste natus error sit voluptatem accus-antium doloremque laudantium,</p></div>
  <div class="abs icon-dot" style="left:329px;top:176px"><svg width="30" height="30" viewBox="0 0 30 30"><text x="15" y="24" text-anchor="middle" font-family="Lato,sans-serif" font-weight="700" font-size="26" fill="#fff">$</text></svg></div>

  <div class="abs benefit left" style="left:80px;top:398px"><h4>Reduced Illness</h4><p>Sed ut perspiciatis unde omnis iste natus error sit voluptatem accus-antium doloremque laudantium,</p></div>
  <div class="abs icon-dot" style="left:329px;top:404px"><svg width="30" height="30" viewBox="0 0 30 30"><rect x="3" y="8" width="24" height="18" rx="3" fill="none" stroke="#fff" stroke-width="2.5"/><rect x="10" y="4" width="10" height="5" fill="none" stroke="#fff" stroke-width="2.5"/><path d="M15 12v10M10 17h10" stroke="#fff" stroke-width="3"/></svg></div>

  <div class="abs icon-dot" style="left:795px;top:176px"><svg width="34" height="30" viewBox="0 0 34 30"><circle cx="17" cy="9" r="5" fill="#fff"/><circle cx="7" cy="12" r="4" fill="#fff"/><circle cx="27" cy="12" r="4" fill="#fff"/><path d="M8 27a9 9 0 0 1 18 0z M0 27a7 7 0 0 1 9-6 M34 27a7 7 0 0 0 -9-6" fill="#fff"/></svg></div>
  <div class="abs benefit" style="left:885px;top:164px"><h4>Increased Flexibility<br>for Parents</h4><p>Sed ut perspiciatis unde omnis iste natus error sit voluptatem accus-antium doloremque laudantium,</p></div>

  <div class="abs icon-dot" style="left:795px;top:404px"><svg width="30" height="30" viewBox="0 0 30 30"><circle cx="12" cy="9" r="6" fill="#fff"/><path d="M1 28a11 11 0 0 1 22 0z" fill="#fff"/><path d="M24 8v10M19 13h10" stroke="#fff" stroke-width="3"/></svg></div>
  <div class="abs benefit" style="left:885px;top:398px;width:270px"><h4>Increased Socialization<br>with other Children<br>vs. Sole Nanny</h4><p>Sed ut perspiciatis unde omnis iste</p></div>
</section>

<h2 class="abs heading blog-title">Our Blog</h2>
<div class="abs blog-card" style="left:87px">
  <div class="ph" role="img" aria-label="Photo of a woman walking a dog in a garden" style="background:linear-gradient(180deg,#7a8f5c,#4f6a3d 60%,#2e3b25)"></div>
  <h3>Lorem Ipsum is simply dummy text of the printing</h3><small>Read More &gt;</small>
</div>
<div class="abs blog-card" style="left:438px">
  <div class="ph" role="img" aria-label="Photo of a child playing with water outdoors" style="background:linear-gradient(180deg,#d8a98a,#a8573f 60%,#5e2f25)"></div>
  <h3>Lorem Ipsum is simply dummy text of the printing</h3><small>Read More &gt;</small>
</div>
<div class="abs blog-card" style="left:787px">
  <div class="ph" role="img" aria-label="Photo of a mother and child smiling at each other" style="background:linear-gradient(180deg,#a9c08b,#7c8f62 60%,#3e4a31)"></div>
  <h3>Lorem Ipsum is simply dummy text of the printing</h3><small>Read More &gt;</small>
</div>

<section class="abs testimonial">
  <div class="abs avatar" role="img" aria-label="Portrait photo of the reviewer"></div>
  <svg class="abs stars" width="96" height="16" viewBox="0 0 96 16">
    <g fill="#ffd23f">
      <path id="star" d="M8 0l2.4 5 5.6.6-4.2 3.8 1.2 5.6L8 12.2 3 15l1.2-5.6L0 5.6 5.6 5z"/>
      <use href="#star" x="20"/><use href="#star" x="40"/><use href="#star" x="60"/><use href="#star" x="80"/>
    </g>
  </svg>
  <div class="abs divider"></div>
  <p class="abs quote">"Sed ut perspiciatis unde omnis iste natus error sit voluptatem accusantium doloremque laudantium, totam rem aperiam, eaque ipsa quae ab illo inventore veritatis et quasi architecto beatae vitae dicta sunt explicabo. Nemo enim ipsam aut odit aut fugit."</p>
  <p class="abs author">- Dana R. Whitlow</p>
  <div class="abs pager">
    <span class="prev"><svg width="8" height="10" viewBox="0 0 8 10"><path d="M6 1L2 5l4 4" stroke="#333" stroke-width="2" fill="none"/></svg></span>
    <span class="next"><svg width="8" height="10" viewBox="0 0 8 10"><path d="M2 1l4 4-4 4" stroke="#fff" stroke-width="2" fill="none"/></svg></span>
  </div>
</section>

<h2 class="abs heading faq-title">Frequently Asked Questions</h2>
<div class="abs faq open" style="top:2674px">
  <div class="q"><span>The standard Lorem Ipsum passage, used since the 1500s?</span><svg width="14" height="14" viewBox="0 0 14 14"><rect x="1" y="1" width="12" height="12" fill="none" stroke="#fff" stroke-width="1.5"/><path d="M4 7h6" stroke="#fff" stroke-width="1.5"/></svg></div>
  <div class="a">Lorem Ipsum is simply dummy text of the printing and typesetting industry. Lorem Ipsum has been the industry's standard dummy text ever since the 1500s, when an unknown printer took a galley of type and scrambled it to make a type specimen book.</div>
</div>
<div class="abs faq" style="top:2826px"><div class="q"><span>Section 1.10.32 of "de Finibus Bonorum et Malorum", written by Varellus in 45 BC</span><svg width="14" height="14" viewBox="0 0 14 14"><rect x="1" y="1" width="12" height="12" fill="none" stroke="#fff" stroke-width="1.5"/><path d="M4 7h6M7 4v6" stroke="#fff" stroke-width="1.5"/></svg></div></div>
<div class="abs faq" style="top:2890px"><div class="q"><span>1914 translation by H. Pellingham</span><svg width="14" height="14" viewBox="0 0 14 14"><rect x="1" y="1" width="12" height="12" fill="none" stroke="#fff" stroke-width="1.5"/><path d="M4 7h6M7 4v6" stroke="#fff" stroke-width="1.5"/></svg></div></div>
<div class="abs faq" style="top:2954px"><div class="q"><span>The standard Lorem Ipsum passage, used since the 1500s?</span><svg width="14" height="14" viewBox="0 0 14 14"><rect x="1" y="1" width="12" height="12" fill="none" stroke="#fff" stroke-width="1.5"/><path d="M4 7h6M7 4v6" stroke="#fff" stroke-width="1.5"/></svg></div></div>
<div class="abs faq" style="top:3018px"><div class="q"><span>The standard Lorem Ipsum passage, used since the 1500s?</span><svg width="14" height="14" viewBox="0 0 14 14"><rect x="1" y="1" width="12" height="12" fill="none" stroke="#fff" stroke-width="1.5"/><path d="M4 7h6M7 4v6" stroke="#fff" stroke-width="1.5"/></svg></div></div>

<section class="abs newsletter" role="img" aria-label="Background photo of a city skyline at dusk">
  <h2 class="abs heading nl-title">NEWSLETTER SIGN UP</h2>
  <p class="abs nl-sub">Lorem ipsum dolor sit amet, consectetur adipisicing elit sed do<br>eiusmod ut labore et dolore</p>
  <div class="abs nl-input">Enter your email...</div>
  <div class="abs nl-btn">SUBSCRIBE</div>
  <div class="abs social">
    <span style="background:#3b5998"></span><span style="background:#1da1f2"></span><span style="background:#dd4b39"></span><span style="background:#e52d27"></span><span style="background:#c13584"></span>
  </div>
</section>

<footer class="abs footer">
  <div class="brand"><span class="dot"></span>Bright Pram Hub</div>
  <div class="abs vline" style="left:449px"></div>
  <div class="abs vline" style="left:915px"></div>
  <div class="abs contact">
    <h4 class="foot-h">Contact Info:</h4>
    <ul>
      <li><svg width="12" height="16" viewBox="0 0 12 16"><path d="M6 0a6 6 0 0 1 6 6c0 4-6 10-6 10S0 10 0 6a6 6 0 0 1 6-6z" fill="#888"/><circle cx="6" cy="6" r="2.2" fill="#fff"/></svg><span>Bright Pram Hub<br>418 Marlowe Avenue, Fairbrook, Ohio, 44012.</span></li>
      <li><svg width="14" height="14" viewBox="0 0 14 14"><path d="M3 0l3 3-2 2a9 9 0 0 0 5 5l2-2 3 3-2 3C6 14 0 8 0 2z" fill="#888"/></svg><span>+1 555 210 4477</span></li>
      <li><svg width="14" height="12" viewBox="0 0 14 12"><rect x="0" y="0" width="14" height="12" rx="1" fill="#888"/><path d="M1 1l6 5 6-5" stroke="#fff" stroke-width="1.3" fill="none"/></svg><span>hello@brightpramhub.net</span></li>
    </ul>
  </div>
  <div class="abs links">
    <h4 class="foot-h">Quick Links:</h4>
    <ul>
      <li>&gt; What We Offer</li><li>&gt; Child Care</li><li>&gt; Senior Care</li><li>&gt; Pet Care</li><li>&gt; Housekeeping</li><li>&gt; How It Works</li><li>&gt; Contact US</li>
    </ul>
  </div>
  <div class="abs footline"></div>
  <p class="abs copy">Copyright © 2018 Bright Pram Hub. All rights reserved.</p>
</footer>

</body>
</html>
```